Company brochure for our unique consulting business

We are a small consulting business offering a unique set of services to our clients.. In simple terms we are a business improvement consultancy helping our clients get the best out of their businesses. We work with clients across multiple sectors and deliver a variety of services. We want to put together a brochure to cover these main themes:1. Who we are2. What we do3. The type of people we employ4. The sectors we work inWhile the brochure needs to have a certain corporate feel to it, we don't want it to be "boring" or "stiff". We would like it to have a slightly "friendly" or "informal" feel to it, to reflect the type of organisation we are.We have a company website http://brevalconsultingpartners.net , however we do not want to directly replicate the content or feel as we recognise it needs updating.We would like the brochure to be A4 portrait format. We anticipate requiring 12 sides (including covers) but we are happy to be guided on this based on the content we have provided.The attached ppt file gives the detail of the content to be included and also shows the proposed pagination. For the front cover we would like to try 2 versions, one with the BCP logo and one with the Breval Consulting Partners logo (a file of both is attached)One of the most important pages will be the "Our Services" page. We would like this to cover the centre fold. In the ppt file we have shown an example layout, but this is where we need most help - we are clearly not graphic designers! This page will be the most used page in sales meetings etc.Also attached is the following:1. file for our BrevalConsulting Partners company logo.2. File for our BCP company logo3. Files for Derek's signatures (for under photos) - Owen's to follow4. Photo of Derek & Owen (person in purple shirt to be cropped out)Thank you and really excited to see what everyone comes back with.Derek & Owen

Target Market(s)

Very broad - Manufacturing, Healthcare, Hospitality

Industry/Entity Type

Management Consulting

Font styles to use
Other font styles liked:
• We use Swiss721, but happy to be guided by designer

Colors
3276b5
85abd2
0355a3
333333
5c5c5c
9d9d9d
d9d9d9

Requirements
Must have
• Corporate feel
Nice to have
• Slightly friendly feel
• Our standard "blue" is (CORRECTION) - R55 G96 B146 #376092 and our standard grey is R197 G178, B179 - #B3B2B2, which we would like to keep, but other colours we are happy to be guided on. Brand guidelines attached.

```html
<!DOCTYPE html>
<html lang="en">
<head>
<meta charset="utf-8">
<title>Breval Consulting Partners – Brochure Covers</title>
<link href="https://fonts.googleapis.com/css2?family=Montserrat:wght@700&family=Raleway:wght@400;500;600;700&display=swap" rel="stylesheet">
<style>
  :root {
    --backdrop: #666666;
    --cover-tint: #e8f0f8;
    --halo: #f3f7fb;
    --ring: #85abd2;
    --ring-light: #c3d6eb;
    --ink: #1a1a1a;
    --brand-navy: #1f3c8f;
    --accent: #7ba3d3;
    --body-grey: #6a6a6a;
    --paper: #ffffff;
  }
  * { margin: 0; padding: 0; box-sizing: border-box; }
  html, body { width: 1200px; height: 1200px; overflow: hidden; }
  body { background: var(--backdrop); font-family: "Raleway", sans-serif; position: relative; }

  .spread {
    position: absolute; left: 40px; top: 205px;
    width: 1120px; height: 790px;
    background: var(--paper); overflow: hidden;
  }
  .spread__artwork { position: absolute; inset: 0; }

  .back-cover__contact { position: absolute; left: 33px; top: 522px; }
  .contact__title {
    font-family: "Montserrat", sans-serif; font-weight: 700;
    font-size: 17px; color: var(--brand-navy); margin-bottom: 10px;
  }
  .contact__row {
    display: flex; align-items: flex-start; gap: 9px;
    font-size: 12.5px; line-height: 13.5px; color: var(--body-grey);
    margin-bottom: 5px;
  }
  .contact__row svg { flex: none; width: 15px; height: 14px; margin-top: 0; }
  .contact__row--tight { margin-bottom: 3px; }
  .back-cover__url {
    position: absolute; left: 33px; top: 663px;
    font-size: 7.5px; font-weight: 700; color: var(--accent);
  }

  .front-cover__panel {
    position: absolute; left: 761px; top: 515px; right: 0; bottom: 0;
    background: var(--paper);
  }
  .front-cover__name {
    position: absolute; left: 44px; top: 28px;
    font-weight: 600; color: var(--ink); line-height: 1;
  }
  .front-cover__name-main { display: block; font-size: 44px; letter-spacing: -0.5px; }
  .front-cover__name-sub { display: block; font-size: 21px; margin-top: 4px; }
  .front-cover__tagline {
    position: absolute; left: 45px; top: 126px; width: 290px;
    font-size: 12px; line-height: 14px; color: var(--accent);
  }
</style>
</head>
<body>
  <main class="spread">
    <svg class="spread__artwork" width="1120" height="790" viewBox="0 0 1120 790">
      <rect class="cover-tint" x="0" y="0" width="1120" height="682" fill="var(--cover-tint)"/>
      <circle class="halo" cx="761" cy="368" r="319" fill="var(--halo)"/>
      <path class="arc arc--lower" d="M482 368 A279 279 0 0 0 761 647" fill="none" stroke="var(--ring-light)" stroke-width="22"/>
      <path class="arc arc--upper" d="M761 86 A282 282 0 0 1 1043 368" fill="none" stroke="var(--ring-light)" stroke-width="12"/>
      <circle class="ring" cx="761" cy="368" r="238" fill="none" stroke="var(--ring)" stroke-width="61"/>
      <defs>
        <linearGradient id="photoTone" x1="0" y1="0" x2="1" y2="1">
          <stop offset="0" stop-color="#eeeeee"/>
          <stop offset="0.55" stop-color="#c9c9c9"/>
          <stop offset="1" stop-color="#9a9a9a"/>
        </linearGradient>
      </defs>
      <circle class="team-photo" cx="761" cy="368" r="208" fill="url(#photoTone)" role="img" aria-label="Black and white photo of the two founders smiling at a meeting table"/>
      <rect class="footer-band" x="33" y="708" width="1033" height="10" fill="var(--cover-tint)"/>
    </svg>

    <section class="back-cover__contact">
      <h2 class="contact__title">Contact Us</h2>
      <div class="contact__row">
        <svg viewBox="0 0 14 14" aria-hidden="true"><path d="M7 0.5a4.5 4.5 0 0 0-4.5 4.5c0 3.4 4.5 8.5 4.5 8.5s4.5-5.1 4.5-8.5A4.5 4.5 0 0 0 7 0.5z" fill="var(--accent)"/><circle cx="7" cy="5" r="1.6" fill="var(--cover-tint)"/></svg>
        <span>BCP Limited<br>Millbrook House<br>Quay Lane, Leicester, LE2 7QT</span>
      </div>
      <div class="contact__row contact__row--tight">
        <svg viewBox="0 0 14 14" aria-hidden="true"><circle cx="7" cy="7" r="6.5" fill="var(--accent)"/><path d="M4.6 3.8c.5-.4 1-.3 1.2.2l.5 1.1c.1.4 0 .6-.3.8l-.4.3c.4.9 1.1 1.6 2 2l.3-.4c.2-.3.5-.4.8-.3l1.1.5c.5.2.6.7.2 1.2-.6.8-1.6.9-2.6.4A7 7 0 0 1 4.2 6.4c-.5-1-.4-2 .4-2.6z" fill="var(--paper)"/></svg>
        <span>+44 (0) 1162 550174</span>
      </div>
      <div class="contact__row">
        <svg viewBox="0 0 14 14" aria-hidden="true"><rect x="0.5" y="2.5" width="13" height="9" fill="var(--accent)"/><path d="M0.5 2.5 7 8l6.5-5.5" fill="none" stroke="var(--cover-tint)" stroke-width="1.1"/></svg>
        <span>enquiries@brevalgroup.net</span>
      </div>
    </section>
    <p class="back-cover__url">www.brevalgroup.net</p>

    <section class="front-cover__panel">
      <h1 class="front-cover__name">
        <span class="front-cover__name-main">Breval</span>
        <span class="front-cover__name-sub">Consulting Partners</span>
      </h1>
      <p class="front-cover__tagline">At BCP we constantly strive to deliver the best possible value for our clients. Importantly we recognize, it's our clients that define value, not us.</p>
    </section>
  </main>
</body>
</html>
```